Kestrel Home Business Card Design

We need a business card for a Building company based in Queensland, Australia. Our colours are orange black and we do base all our homes design names and other aspect of our business on astrology. We want the consumer to perceive the company as professional and to attract investors to our company.We have over 20 years in the building industry.We pride ourselves on our innovation of designs and making the building process for anyone from families to investor a smooth and simple experience.
Business
Amelia Prichard0411752116PO Box 454, Mudgeerbaameliaprichard@zodiachomes.com

```html
<!DOCTYPE html>
<html lang="en">
<head>
<meta charset="utf-8">
<title>Kestrel Homes – Business Card</title>
<link rel="stylesheet" href="https://fonts.googleapis.com/css2?family=Poppins:wght@600&family=Questrial&family=Open+Sans:wght@400&display=swap">
<style>
  :root {
    --orange: #f5851f;
    --orange-deep: #f07a12;
    --orange-light: #f7941d;
    --ink: #1c1c1c;
    --paper: #ffffff;
    --backdrop: #e6e9ea;
    --muted: #3a3a3a;
  }
  * { margin: 0; padding: 0; box-sizing: border-box; }
  html, body { width: 1200px; height: 900px; overflow: hidden; }
  body {
    background: var(--backdrop);
    display: flex;
    flex-direction: column;
    align-items: center;
    justify-content: center;
    gap: 30px;
  }
  .card {
    width: 700px;
    height: 400px;
    position: relative;
    overflow: hidden;
    box-shadow: 0 6px 18px rgba(0,0,0,0.12);
  }

  /* Front */
  .card-front { background: var(--paper); }
  .edge-band {
    position: absolute; left: 0; top: 0; bottom: 0;
    width: 14px; background: var(--orange);
  }
  .brand-mark {
    position: absolute; left: 62px; top: 96px;
    width: 58px; height: 58px; border-radius: 50%;
    background: var(--ink);
  }
  .brand-row {
    position: absolute; left: 62px; right: 56px; top: 170px;
    display: flex; align-items: flex-end; gap: 18px;
  }
  .brand-name {
    font-family: "Poppins", sans-serif; font-weight: 600;
    font-size: 34px; line-height: 1; color: var(--ink);
    letter-spacing: -0.5px; white-space: nowrap;
  }
  .brand-rule {
    flex: 1; height: 2px; background: var(--orange); margin-bottom: 8px;
  }
  .person-name {
    font-family: "Questrial", sans-serif; font-size: 28px;
    color: var(--ink); letter-spacing: 1px; white-space: nowrap;
    line-height: 1;
  }
  .divider {
    position: absolute; left: 160px; right: 56px; top: 245px;
    height: 2px; background: var(--orange);
  }
  .contact-list {
    position: absolute; left: 62px; bottom: 44px;
    list-style: none;
    font-family: "Open Sans", sans-serif; font-size: 15px;
    color: var(--muted); letter-spacing: 0.6px;
  }
  .contact-list li { display: flex; align-items: center; gap: 12px; line-height: 24px; }
  .contact-icon { width: 12px; height: 12px; fill: var(--orange); flex: none; }

  /* Back */
  .card-back {
    background: linear-gradient(135deg, var(--orange-light), var(--orange-deep));
    display: flex; flex-direction: column; align-items: center; justify-content: center;
    gap: 26px;
  }
  .back-mark {
    width: 120px; height: 120px; border-radius: 50%;
    background: var(--ink);
  }
  .back-name {
    font-family: "Poppins", sans-serif; font-weight: 600;
    font-size: 74px; line-height: 1; color: var(--ink); letter-spacing: -1px;
  }
</style>
</head>
<body>

  <section class="card card-front">
    <div class="edge-band"></div>
    <div class="brand-mark"></div>
    <div class="brand-row">
      <span class="brand-name">Kestrel Homes</span>
      <span class="brand-rule"></span>
      <span class="person-name">Harriet Colvane</span>
    </div>
    <div class="divider"></div>
    <ul class="contact-list">
      <li>
        <svg class="contact-icon" viewBox="0 0 24 24" aria-hidden="true"><path d="M6.6 10.8a15.1 15.1 0 0 0 6.6 6.6l2.2-2.2c.3-.3.7-.4 1-.2 1.1.4 2.3.6 3.6.6.6 0 1 .4 1 1V20c0 .6-.4 1-1 1A17 17 0 0 1 3 4c0-.6.4-1 1-1h3.5c.6 0 1 .4 1 1 0 1.3.2 2.5.6 3.6.1.3 0 .7-.2 1z"/></svg>
        0487309625
      </li>
      <li>
        <svg class="contact-icon" viewBox="0 0 24 24" aria-hidden="true"><path d="M12 2a7 7 0 0 0-7 7c0 5.2 7 13 7 13s7-7.8 7-13a7 7 0 0 0-7-7zm0 9.5A2.5 2.5 0 1 1 12 6.5a2.5 2.5 0 0 1 0 5z"/></svg>
        PO Box 872, Wattlebrook
      </li>
      <li>
        <svg class="contact-icon" viewBox="0 0 24 24" aria-hidden="true"><path d="M2 5h20v14H2z M2 5l10 8 10-8" fill="none" stroke="#f5851f" stroke-width="2.4"/></svg>
        harrietcolvane@kestrelhomes.example
      </li>
    </ul>
  </section>

  <section class="card card-back">
    <div class="back-mark"></div>
    <div class="back-name">Kestrel Homes</div>
  </section>

</body>
</html>
```